New B2C website design to help dads be better dads

DadHarbor is a website to help dads be the “best dad you can be.”

We require our website to be designed into a PSD format, no coding necessary.

The general concept is a two-page design. The first page is the login page, the second page is the home page. Once at the home page, rather than navigating to and from different pages, the user will push and pull through different visual and functional layers of the hierarchy. In theory, this should add to the user experience by having a visual anchor of where they are (through layered pagination) as well as improving loading times since the new information should only be a delta in data load versus a brand new page load.

The general look-and-feel we are going for is clean, simple, minimal. This means that the winning design will show us a good eye for web-optimized typography, good use of white (negative) space, and good use of a visually pleasing grid.

We require a total of 6 page "views" plus the landing page. We note that many of the views are similar to one another.
Landing page
Milestone view
Task view
Content view, articles
Content view, products
Search view
What's new view

Please review all of the additional information provided as well as the attachments for examples.

We provide the following websites as good references for:

Typography:
http://example-kelvorn.com/journal/

Use of white space:
http://www.trenvaskit.com/
http://moldrefin.com/

Example for “scrolling” page concept as well as good balance of color, typography, and white space:
http://www.qorbitalmeet.eu/

Please contact us with questions so that we can guide your design effort.
Updates

Hello designers,

The following information is added to help guide the design process:

1.  For the text dialogue below the landing page, please assume the following word count:
"why are we making dad harbor?": 250 words
"who are we?" 200 words
"what's the deal with the penguin logo?" 300 words

For the social media links, please see http://www.gravelplumbs.com/
Notice the floating "social" bar that is always to the right.  This is the concept we are going for, please try to implement this as you see fit. 

Target Market(s)

Fathers of young children ages 0-6 years old.

Industry/Entity Type

Product

Font styles to use
Sans Serif

Requirements
Must have
• Clean lines, minimal design concept

Incorporation of our logo (see attached document)

Header content is static for all views after landing page, see example

This page WILL be responsive, please keep that in mind when designing
The timeline bar should be to the left, with the timeline bar’s “milestones” also being responsive.

Designer is free to suggest font types, but any fonts used must be royalty-free and web-optimized. We request a minimum number of font types as well as fonts that load relatively fast. We reinforce that visually appealing typography is a significant factor in the winning design choice.

While we are not expecting the winning design to include code, please keep in mind that the final implementation needs to be optimized for desktop, tablet, and mobile platforms.

If you are using stock photography that is not generated by you, please provide where/how we can obtain imagery, as well as price.

All custom graphics must be available in original formats; Photoshop/GIMP layered files for layout design, and vector formats for logos, icons and other graphical elements.

Please incorporate “Blue” into design elements as you see fit, as the RGB 67 74 169 Blue is the primary color used in our brand. The complement to this blue is 255 202 0, a brownish orange. Feel free to use this color as well, although please keep it to a lesser amount.

Background color is your choice, do not feel the need to use the grey.
Should not have
• Excessive graphical content such that it affects loading times

Excessive use of too many font types such that it affects loading times

```html
<!DOCTYPE html>
<html lang="en">
<head>
<meta charset="utf-8">
<title>DadHarbor – Home</title>
<link rel="stylesheet" href="https://fonts.googleapis.com/css2?family=Francois+One&family=Noto+Sans:wght@400;700&display=swap">
<style>
  :root {
    --navy: #1f2d6e;
    --brand-blue: #434aa9;
    --accent: #f2a900;
    --panel: #e3e3e3;
    --line: #c9c9c9;
    --text: #333333;
    --muted: #555555;
    --white: #ffffff;
    --star-on: #f4b400;
    --star-off: #cfcfcf;
    --badge-base: #e8541a;
    --grass: #6cb43c;
  }
  * { box-sizing: border-box; margin: 0; padding: 0; }
  html, body { width: 1200px; height: 1003px; overflow: hidden; background: var(--white); }
  body { font-family: "Noto Sans", Arial, sans-serif; color: var(--text); }
  .canvas { position: relative; width: 1200px; height: 1003px; overflow: hidden; }

  /* Header */
  .site-header {
    position: absolute; left: 0; top: 0; width: 1200px; height: 138px;
    background: linear-gradient(#e9e9e9, #ffffff 70%);
    border-bottom: 4px solid var(--accent);
  }
  .brand { position: absolute; left: 34px; top: 52px; display: flex; align-items: center; gap: 8px; }
  .brand-mark { width: 22px; height: 22px; border-radius: 50%; background: var(--navy); }
  .brand-name { font-size: 19px; font-weight: 700; color: var(--navy); }
  .welcome {
    position: absolute; left: 192px; top: 12px;
    font-family: "Francois One", "Arial Narrow", sans-serif; font-size: 36px; color: #111; letter-spacing: .3px;
  }
  .score { position: absolute; left: 192px; top: 86px; font-size: 16px; color: #222; }
  .score strong { color: var(--navy); }
  .search-field {
    position: absolute; left: 438px; top: 77px; width: 300px; height: 43px;
    background: var(--white); border: 1px solid #d4d4d4; border-radius: 3px;
  }
  .btn {
    position: absolute; height: 43px; background: var(--navy); color: var(--white);
    font-size: 16px; font-weight: 700; letter-spacing: .5px; border-radius: 3px;
    display: flex; align-items: center; justify-content: center;
  }
  .btn-search { left: 749px; top: 77px; width: 113px; }
  .btn-logout { left: 1058px; top: 77px; width: 114px; }
  .account-link { position: absolute; left: 959px; top: 88px; font-size: 16px; color: #222; }

  /* Timeline */
  .timeline-line { position: absolute; left: 91px; top: 142px; width: 2px; height: 861px; background: var(--line); }
  .milestone { position: absolute; left: 6px; width: 70px; height: 80px; }
  .milestone-label {
    position: absolute; left: 8px; top: 12px; width: 54px; text-align: center; line-height: 1;
    font-size: 20px; color: #222;
  }
  .milestone-label small { display: block; font-size: 15px; margin-top: 1px; }
  .expand {
    position: absolute; width: 30px; height: 30px; border-radius: 50%;
    background: var(--white); border: 2px solid #b9b9b9; color: var(--navy);
    font-size: 24px; font-weight: 700; line-height: 24px; text-align: center;
  }

  /* Panel */
  .latest-panel {
    position: absolute; left: 72px; top: 192px; width: 1098px; height: 762px;
    background: var(--panel); border-radius: 22px 40px 14px 30px;
  }
  .latest-panel::before {
    content: ""; position: absolute; left: 0; top: 50px; width: 38px; height: 712px; background: var(--white);
  }
  .latest-title { position: absolute; left: 114px; top: 208px; font-size: 19px; color: #111; }

  .related {
    position: absolute; left: 132px; top: 250px; width: 262px; height: 345px;
    background: var(--white); border: 1px solid #d0d0d0; padding: 12px 20px;
  }
  .related h2 { font-size: 20px; font-weight: 400; color: var(--navy); line-height: 1.2; margin-bottom: 14px; }
  .task { display: flex; align-items: center; gap: 16px; height: 33px; font-size: 17px; color: #333; }
  .check { width: 18px; height: 18px; border-radius: 3px; background: #ececec; border: 1px solid #d8d8d8; flex: none; }
  .check.on { background: #7fb8ea; border-color: #5f9fd8; display: flex; align-items: center; justify-content: center; }

  .card { position: absolute; width: 260px; background: var(--white); padding: 10px; }
  .card-media { width: 240px; height: 144px; }
  .media-photo { background: linear-gradient(135deg, #4a4a4a, #9a8068 55%, #c9b8a0); }
  .media-product { background: linear-gradient(135deg, #f2f2f2, #b7b99a 50%, #eeeeee); }
  .card-type { margin-top: 10px; font-size: 16px; font-weight: 700; color: var(--navy); letter-spacing: .3px; }
  .card-meta { display: flex; justify-content: space-between; align-items: center; margin-top: 8px; font-size: 15px; color: var(--navy); }
  .stars { display: flex; gap: 2px; }
  .card-text { margin-top: 14px; font-size: 15px; line-height: 1.3; color: #333; }

  .sort { position: absolute; left: 1010px; top: 245px; font-size: 15px; color: #222; }
  .sort-select {
    position: absolute; left: 1010px; top: 268px; width: 115px; height: 28px; background: var(--white);
    border: 1px solid #d0d0d0; font-size: 14px; padding: 5px 7px; color: #333;
  }
  .sort-select svg { position: absolute; right: 8px; top: 10px; }

  .share-bar {
    position: absolute; left: 1140px; top: 214px; width: 62px; height: 258px;
    background: #eeeae0; border: 1px solid #c9c2b0; border-radius: 8px 0 0 8px;
  }
  .share-bar span { position: absolute; left: 0; top: 8px; width: 62px; text-align: center; font-size: 15px; color: #222; }
  .share-link { position: absolute; left: 10px; width: 48px; height: 48px; border-radius: 50%; background: var(--navy); }
</style>
</head>
<body>
<div class="canvas">

  <header class="site-header">
    <div class="brand"><span class="brand-mark"></span><span class="brand-name">DadHarbor</span></div>
    <h1 class="welcome">Welcome Greg, what would you like to do today?</h1>
    <p class="score">Super Dad Score: <strong>10,500</strong></p>
    <div class="search-field"></div>
    <div class="btn btn-search">SEARCH</div>
    <span class="account-link">My account</span>
    <div class="btn btn-logout">LOGOUT</div>
  </header>

  <div class="timeline-line"></div>

  <div class="latest-panel"></div>
  <p class="latest-title">What’s the latest?</p>

  <div class="milestone" style="top:180px">
    <svg width="70" height="80" viewBox="0 0 70 80">
      <path d="M8 70 V26 Q8 2 35 2 Q62 2 62 26 V70 Z" fill="#fff" stroke="#cfcfcf"/>
      <rect x="8" y="56" width="54" height="16" fill="var(--badge-base)"/>
      <path d="M2 74 L8 62 L11 72 L15 64 L18 74 Z" fill="var(--grass)"/>
    </svg>
    <div class="milestone-label">0<small>mo</small></div>
  </div>
  <div class="expand" style="left:76px;top:206px">+</div>

  <div class="milestone" style="top:900px">
    <svg width="70" height="80" viewBox="0 0 70 80">
      <path d="M8 70 V26 Q8 2 35 2 Q62 2 62 26 V70 Z" fill="#fff" stroke="#cfcfcf"/>
      <rect x="8" y="56" width="54" height="16" fill="var(--badge-base)"/>
      <path d="M2 74 L8 62 L11 72 L15 64 L18 74 Z" fill="var(--grass)"/>
    </svg>
    <div class="milestone-label">0<small>mo</small></div>
  </div>
  <div class="expand" style="left:76px;top:926px">+</div>

  <section class="related">
    <h2>Related milestones and tasks include:</h2>
    <div class="task"><span class="check"></span>Buy a crib</div>
    <div class="task"><span class="check"></span>As semble the crib</div>
    <div class="task"><span class="check"></span>Buy a stroller</div>
    <div class="task"><span class="check on"><svg width="12" height="10" viewBox="0 0 12 10"><path d="M1 5 L4.5 8.5 L11 1" fill="none" stroke="#1f4f8a" stroke-width="2"/></svg></span>Buy a carseat</div>
    <div class="task"><span class="check"></span>Install a carseat</div>
    <div class="task"><span class="check"></span>Learn to change a diaper</div>
    <div class="task"><span class="check"></span>Learn to hold a baby</div>
    <div class="task"><span class="check"></span>Set a feeding schedule</div>
  </section>

  <svg width="0" height="0" style="position:absolute">
    <defs>
      <symbol id="star" viewBox="0 0 20 20"><polygon points="10,1 12.6,7 19,7.4 14,11.6 15.6,18.6 10,14.8 4.4,18.6 6,11.6 1,7.4 7.4,7"/></symbol>
    </defs>
  </svg>

  <article class="card" style="left:424px;top:248px;height:329px">
    <div class="card-media media-photo" role="img" aria-label="Photo of a father buckling his baby into a car seat"></div>
    <p class="card-type">ARTICLE</p>
    <div class="card-meta">
      <div class="stars"><svg width="20" height="20" fill="var(--star-on)"><use href="#star"/></svg><svg width="20" height="20" fill="var(--star-on)"><use href="#star"/></svg><svg width="20" height="20" fill="var(--star-on)"><use href="#star"/></svg><svg width="20" height="20" fill="var(--star-off)"><use href="#star"/></svg><svg width="20" height="20" fill="var(--star-off)"><use href="#star"/></svg></div>
      <span>3,121 ratings</span>
    </div>
    <p class="card-text">I went out to buy my first car seat and had to earn my PhD in car seats, Newtonian physics, and anti-stain technology...</p>
  </article>

  <article class="card" style="left:721px;top:248px;height:329px">
    <div class="card-media media-product" role="img" aria-label="Product photo of a stroller with a matching infant carrier"></div>
    <p class="card-type">PRODUCT</p>
    <div class="card-meta">
      <div class="stars"><svg width="20" height="20" fill="var(--star-on)"><use href="#star"/></svg><svg width="20" height="20" fill="var(--star-on)"><use href="#star"/></svg><svg width="20" height="20" fill="var(--star-on)"><use href="#star"/></svg><svg width="20" height="20" fill="var(--star-off)"><use href="#star"/></svg><svg width="20" height="20" fill="var(--star-off)"><use href="#star"/></svg></div>
      <span>9,102 likes</span>
    </div>
    <p class="card-text">The Brennick XT stroller is this year’s hottest stroller, for more reasons than are obvious. What we particularly like about it is...</p>
  </article>

  <article class="card" style="left:424px;top:606px;height:328px">
    <div class="card-media media-photo" role="img" aria-label="Photo of a father buckling his baby into a car seat"></div>
    <p class="card-type">ARTICLE</p>
    <div class="card-meta">
      <div class="stars"><svg width="20" height="20" fill="var(--star-on)"><use href="#star"/></svg><svg width="20" height="20" fill="var(--star-on)"><use href="#star"/></svg><svg width="20" height="20" fill="var(--star-on)"><use href="#star"/></svg><svg width="20" height="20" fill="var(--star-off)"><use href="#star"/></svg><svg width="20" height="20" fill="var(--star-off)"><use href="#star"/></svg></div>
      <span>1,595 likes</span>
    </div>
    <p class="card-text">I learned something new this week which made my penny-pinching side just giddy. Car seats double as airplane...</p>
  </article>

  <article class="card" style="left:721px;top:606px;height:328px">
    <div class="card-media media-photo" role="img" aria-label="Photo of a father buckling his baby into a car seat"></div>
    <p class="card-type">ARTICLE</p>
    <div class="card-meta">
      <div class="stars"><svg width="20" height="20" fill="var(--star-on)"><use href="#star"/></svg><svg width="20" height="20" fill="var(--star-on)"><use href="#star"/></svg><svg width="20" height="20" fill="var(--star-on)"><use href="#star"/></svg><svg width="20" height="20" fill="var(--star-off)"><use href="#star"/></svg><svg width="20" height="20" fill="var(--star-off)"><use href="#star"/></svg></div>
      <span>9,007 likes</span>
    </div>
    <p class="card-text">Don’t forget your go-bag essentials! Camping gear aside, Trailpack Co. has assembled a great kit to take...</p>
  </article>

  <p class="sort">Sort by:</p>
  <div class="sort-select">Most recent
    <svg width="10" height="6" viewBox="0 0 10 6"><path d="M0 0 H10 L5 6 Z" fill="var(--navy)"/></svg>
  </div>

  <aside class="share-bar">
    <span>Share</span>
    <div class="share-link" style="top:31px" role="img" aria-label="Share link"></div>
    <div class="share-link" style="top:86px" role="img" aria-label="Share link"></div>
    <div class="share-link" style="top:141px" role="img" aria-label="Share link"></div>
    <div class="share-link" style="top:196px" role="img" aria-label="Share link"></div>
  </aside>

</div>
</body>
</html>
```